Business Card Design

Looking for business card designs for a new business. there will be two cards of the same design (both lots of information below in contact info). We would like the logo diagonally across the card with the information split above and below the logo similar to sketch. happy to look at similar alternatives
Please use same colours as in logo design

Industry/Entity Type

Business

Contact Information for Business Card

Dwight Halloran
mob - 0491 738 204
ph - 02 6148 3920
fax - 02 6148 3975
email - dwight@kestrelbeams.com.au
14 Larkmoor Road, Brindle Creek NSW 2799

Colin Marchetti
mob - 0438 912 557
ph - 02 6148 3920
fax - 02 6148 3975
email - colin@kestrelbeams.com.au

```html
<!DOCTYPE html>
<html lang="en">
<head>
<meta charset="utf-8">
<title>Kestrel Beams – Business Cards</title>
<link href="https://fonts.googleapis.com/css2?family=Source+Sans+3:wght@400;600;700&display=swap" rel="stylesheet">
<style>
  :root {
    --teal: #137b72;
    --teal-text: #1f7670;
    --ink: #111111;
    --paper: #ffffff;
    --backdrop: #e8e5e0;
    --edge: #2a2a2a;
  }
  * { box-sizing: border-box; margin: 0; padding: 0; }
  html, body {
    width: 1200px; height: 1191px; overflow: hidden;
    background: var(--backdrop);
    font-family: "Source Sans 3", "Myriad Pro", Arial, sans-serif;
  }
  .card {
    position: absolute;
    width: 942px; height: 537px;
    background: var(--paper);
    border: 1.5px solid var(--edge);
    border-radius: 40px;
    overflow: hidden;
  }
  .card--front { left: 26px; top: 47px; }
  .card--back  { left: 223px; top: 625px; }

  .wordmark {
    position: absolute;
    display: flex; align-items: center; gap: 20px;
    color: var(--ink);
    font-weight: 700;
    line-height: 1;
    white-space: nowrap;
  }
  .wordmark__square { background: var(--teal); flex: none; }
  .card--front .wordmark { left: 0; right: 0; justify-content: center; top: 92px; font-size: 82px; }
  .card--front .wordmark__square { width: 62px; height: 62px; }
  .card--back .wordmark  { left: 0; right: 0; justify-content: center; top: 205px; font-size: 96px; }
  .card--back .wordmark__square { width: 70px; height: 70px; }

  .front-wave { position: absolute; inset: 0; width: 100%; height: 100%; }

  .holder-name {
    position: absolute; left: 0; right: 0; top: 280px;
    text-align: center;
    color: var(--teal-text);
    font-weight: 700; font-size: 32px;
  }
  .contact {
    position: absolute; left: 0; right: 0;
    text-align: center;
    color: var(--paper);
    font-size: 23px; font-weight: 400;
    display: flex; justify-content: center; align-items: center; gap: 6px;
    white-space: nowrap;
  }
  .contact--phones { top: 400px; }
  .contact--email  { top: 443px; }
  .contact--address { top: 492px; }
  .contact__item { display: inline-flex; align-items: center; gap: 5px; }
  .icon { width: 20px; height: 20px; fill: var(--paper); flex: none; }

  .website {
    position: absolute; left: 0; right: 0; top: 425px;
    text-align: center;
    color: #222;
    font-size: 27px; letter-spacing: 2px;
  }
  .website strong { font-weight: 700; }
</style>
</head>
<body>

<section class="card card--front" aria-label="Business card front">
  <div class="wordmark"><span class="wordmark__square"></span>Kestrel Beams</div>

  <svg class="front-wave" viewBox="0 0 942 537" preserveAspectRatio="none" aria-hidden="true">
    <path d="M0 308 Q471 450 942 295 L942 537 L0 537 Z" fill="var(--teal)"/>
    <path d="M0 291 Q471 434 942 280" fill="none" stroke="var(--ink)" stroke-width="4"/>
  </svg>

  <p class="holder-name">Colin Marchetti</p>

  <p class="contact contact--phones">
    <span class="contact__item">
      <svg class="icon" viewBox="0 0 24 24" aria-label="phone"><path d="M6.6 10.8a15 15 0 0 0 6.6 6.6l2.2-2.2a1 1 0 0 1 1-.25 11.4 11.4 0 0 0 3.6.57 1 1 0 0 1 1 1V20a1 1 0 0 1-1 1A17 17 0 0 1 3 4a1 1 0 0 1 1-1h3.5a1 1 0 0 1 1 1c0 1.25.2 2.45.57 3.57a1 1 0 0 1-.25 1z"/></svg>
      02 6148 3920
    </span>
    <span class="contact__item">
      <svg class="icon" viewBox="0 0 24 24" aria-label="mobile"><path d="M8 1h8a2 2 0 0 1 2 2v18a2 2 0 0 1-2 2H8a2 2 0 0 1-2-2V3a2 2 0 0 1 2-2zm0 3v12h8V4zm4 14a1.3 1.3 0 1 0 0 2.6A1.3 1.3 0 0 0 12 18z"/></svg>
      0438 912 557
    </span>
    <span class="contact__item">
      <svg class="icon" viewBox="0 0 24 24" aria-label="fax"><path d="M7 2h8l3 3v4h1a3 3 0 0 1 3 3v7h-4v3H6v-3H2v-7a3 3 0 0 1 3-3h2zm2 2v5h7V6h-2V4zm-1 11v5h8v-5z"/></svg>
      02 6148 3975
    </span>
  </p>
  <p class="contact contact--email">
    <span class="contact__item">
      <svg class="icon" viewBox="0 0 24 24" aria-label="email"><path d="M2 6h20v13H2zm2 2v.5l8 5 8-5V8l-8 5z"/></svg>
      colin@kestrelbeams.com.au
    </span>
  </p>
  <p class="contact contact--address">14 Larkmoor Road, Brindle Creek NSW 2799</p>
</section>

<section class="card card--back" aria-label="Business card back">
  <div class="wordmark"><span class="wordmark__square"></span>Kestrel Beams</div>
  <p class="website">www.<strong>kestrelbeams</strong>.com.au</p>
</section>

</body>
</html>
```